Business Card for Coach - ready to print

Design Business Card ready to order prints www.lukasbrenner.coach

* An Overview / Background of the Business & Services
· Coaching
· Personal growth
* The Target Market / Audience you are trying to reach
· private person in different roles (self, familiy, business role)s
* Design Specifics; any preferences or ideas for Style, Colour, Imagery, etc
· See www.lukasbrenner.coach
· "simple" design
· (small) element of surprise / unusual element

* Information that will be placed in the Business Card
· Beratung und Coaching
· Address: Lukas Brenner, Mosering 42, CH-8312 Winterthur, Mobile +41 79 264 53 07
* Do you have an existing website or Facebook page where designers can learn more about your company?
· lukasbrenner.coach

Target Market(s)

private person in different roles (self, familiy, business role)

Industry/Entity Type

Life Coaching

Contact Information for Business Card

Lukas Brenner
Mosering 42
CH-8312 Winterthur

Mobile: +41 79 264 53 07
Email: lubr@alpimail.ch
www.lukasbrenner.coach

Font styles to use
Sans Serif

Colors

Designer to choose colors to be used in the design.

Requirements
Must have
• "simple" design
• element of surprise / unusual element
• Beratung & Coaching
• see www.lukasbrenner.coach for colors and so...
Nice to have
• TA Symbol (three rings on top of each other) - unsual presentation
• QR Code of Website (see if it fits in and still looks good).

```html
<!DOCTYPE html>
<html lang="en">
<head>
<meta charset="utf-8">
<title>Lukas Brenner – Business Card</title>
<link href="https://fonts.googleapis.com/css2?family=Lato:wght@400;700;900&display=swap" rel="stylesheet">
<style>
  :root {
    --stage: #232427;
    --card: #5ec8f4;
    --ink: #111417;
    --ink-soft: #2d4a58;
    --ink-muted: #3c5866;
    --accent-bar: #1a1a1a;
    --portrait-a: #b9bcbf;
    --portrait-b: #7d8287;
    --portrait-ring: #1c1c1c;
  }
  * { box-sizing: border-box; margin: 0; padding: 0; }
  html, body {
    width: 1200px; height: 900px; overflow: hidden;
    background: var(--stage);
    font-family: "Lato", sans-serif;
  }
  .stage {
    position: relative; width: 1200px; height: 900px;
  }
  .card {
    position: absolute; left: 315px;
    width: 570px; height: 326px;
    background: var(--card);
    border-radius: 3px;
    box-shadow: 0 14px 30px rgba(0,0,0,.45);
    overflow: hidden;
  }
  .card--front { top: 90px; }
  .card--back { top: 484px; }

  .portrait {
    position: absolute;
    width: 184px; height: 184px; border-radius: 50%;
    border: 2px solid var(--portrait-ring);
    background: radial-gradient(circle at 55% 40%, var(--portrait-a), var(--portrait-b));
  }
  .card--front .portrait { left: 330px; top: 96px; }
  .card--back .portrait { left: 352px; top: 118px; }

  /* front */
  .identity { position: absolute; left: 40px; top: 30px; }
  .identity__bar {
    position: absolute; left: -14px; top: 0;
    width: 10px; height: 30px; background: var(--accent-bar);
  }
  .identity__name {
    font-weight: 900; font-size: 27px; letter-spacing: .5px;
    color: var(--ink); line-height: 30px;
  }
  .identity__role {
    font-size: 13px; color: var(--ink-muted); margin-top: 1px;
  }
  .address { margin-top: 10px; font-size: 13.5px; line-height: 17px; color: var(--ink-soft); }
  .address__company { font-weight: 700; color: var(--ink); }
  .contacts { list-style: none; margin-top: 6px; font-size: 13.5px; line-height: 19px; color: var(--ink-soft); }
  .contacts li { display: flex; align-items: center; gap: 8px; }
  .contacts svg { width: 13px; height: 13px; flex: none; }

  /* back */
  .services { position: absolute; left: 56px; top: 44px; }
  .services__title {
    font-weight: 900; font-size: 24px; color: var(--ink);
    padding-bottom: 8px; border-bottom: 1px solid rgba(0,0,0,.12);
    width: 130px;
  }
  .services__list { list-style: none; margin-top: 6px; font-size: 21px; line-height: 26px; color: var(--ink-muted); }
</style>
</head>
<body>
<main class="stage">

  <section class="card card--front" aria-label="Business card front">
    <div class="identity">
      <span class="identity__bar"></span>
      <h1 class="identity__name">LUKAS BRENNER</h1>
      <p class="identity__role">Founder &amp; CEO</p>
      <address class="address" style="font-style:normal">
        <div class="address__company">Beratung and Coaching</div>
        <div>Lukas Brenner, Mosering 42</div>
        <div>CH-8312 Winterthur</div>
      </address>
      <ul class="contacts">
        <li>
          <svg viewBox="0 0 16 16"><path d="M4 1.5l2.2 3-1.3 1.6c.9 2 2.4 3.5 4.4 4.4l1.6-1.3 3 2.2-1.2 2.6C7 14 2 9 1.4 2.7z" fill="var(--ink)"/></svg>
          +41 79 264 53 07
        </li>
        <li>
          <svg viewBox="0 0 16 16"><rect x="1" y="3" width="14" height="10" fill="var(--ink)"/><path d="M1.5 3.5L8 9l6.5-5.5" stroke="var(--card)" stroke-width="1.4" fill="none"/></svg>
          lubr@alpimail.ch
        </li>
        <li>
          <svg viewBox="0 0 16 16"><circle cx="8" cy="8" r="7" fill="var(--ink-soft)"/><path d="M1 8h14M8 1c-3 3-3 11 0 14M8 1c3 3 3 11 0 14" stroke="var(--card)" stroke-width="1" fill="none"/></svg>
          www.lukasbrenner.coach
        </li>
      </ul>
    </div>
    <div class="portrait" role="img" aria-label="Round portrait photo of the coach"></div>
  </section>

  <section class="card card--back" aria-label="Business card back">
    <div class="services">
      <h2 class="services__title">SERVIES:</h2>
      <ul class="services__list">
        <li>Coaching</li>
        <li>Personal growth</li>
      </ul>
    </div>
    <div class="portrait" role="img" aria-label="Round portrait photo of the coach"></div>
  </section>

</main>
</body>
</html>
```